Harbor Ledger Funds Bus card and Logo

I need a logo design and Bus card design. The fund focuses on evaluating and investing in minerals (sub-surface rights) and real estate.

Harbor ledger refers to a book of knowledge that each plebe gets when entering the Kelmont Marine Academy (my alma mater)

Target Market(s)

Investors and financial advisors

Contact Information for Business Card

Simple - perhaps a logo with a theme on book of knowledge

Logo Text

Ex Scientia Imperium

Font styles to use
Serif
Sans Serif

Colors

Designer to choose colors to be used in the design.

Requirements
Must have
• memorable logo that is relatively simple

```html
<!DOCTYPE html>
<html lang="en">
<head>
<meta charset="utf-8">
<title>Harbor Ledger Funds – Business Card</title>
<link href="https://fonts.googleapis.com/css2?family=Open+Sans:wght@400;600;700&display=swap" rel="stylesheet">
<style>
  :root {
    --navy: #1f3f94;
    --navy-deep: #16307a;
    --navy-light: #2a52ad;
    --lime: #a6cf2d;
    --paper: #f6f7f8;
    --white: #ffffff;
    --page: #e9eaec;
  }
  * { box-sizing: border-box; margin: 0; padding: 0; }
  html, body { width: 1200px; height: 780px; overflow: hidden; }
  body {
    background: var(--page);
    font-family: "Open Sans", Arial, sans-serif;
    position: relative;
  }
  .card {
    position: absolute;
    top: 235px;
    width: 540px;
    height: 310px;
    border-radius: 4px;
    overflow: hidden;
    box-shadow: 0 6px 18px rgba(0,0,0,0.18);
  }
  .card--front { left: 40px; background: var(--paper); }
  .card--back {
    left: 620px;
    background: radial-gradient(ellipse at 45% 40%, var(--navy-light) 0%, var(--navy) 55%, var(--navy-deep) 100%);
  }
  .card__wave { position: absolute; inset: 0; width: 100%; height: 100%; }

  .brand {
    position: absolute;
    display: flex;
    align-items: center;
    gap: 10px;
    font-weight: 700;
    text-transform: uppercase;
    letter-spacing: 1px;
    line-height: 1.1;
  }
  .brand__dot {
    width: 22px; height: 22px; border-radius: 50%;
    background: var(--lime);
    flex: none;
  }
  .card--front .brand {
    left: 30px; top: 128px;
    color: var(--navy);
    font-size: 21px;
  }
  .card--back .brand {
    left: 50%; top: 50%;
    transform: translate(-50%, -50%);
    color: var(--white);
    font-size: 28px;
  }

  .contact {
    position: absolute;
    left: 320px; top: 34px;
    color: var(--white);
  }
  .contact__name { font-size: 22px; font-weight: 700; line-height: 1.1; }
  .contact__title { font-size: 13px; color: var(--lime); margin-bottom: 22px; }
  .contact__address { font-size: 12.5px; line-height: 1.45; margin-bottom: 20px; }
  .contact__list { list-style: none; font-size: 12.5px; }
  .contact__item { display: flex; align-items: center; gap: 7px; margin-bottom: 4px; }
  .contact__icon { width: 16px; height: 16px; flex: none; }
  .contact__web-accent { color: var(--lime); }
</style>
</head>
<body>

<section class="card card--front" aria-label="Business card front">
  <svg class="card__wave" viewBox="0 0 540 310" preserveAspectRatio="none" aria-hidden="true">
    <defs>
      <linearGradient id="frontBlue" x1="0" y1="0" x2="1" y2="1">
        <stop offset="0" stop-color="#2a52ad"/>
        <stop offset="1" stop-color="#1a3684"/>
      </linearGradient>
    </defs>
    <path d="M290 0 C 240 80, 330 140, 300 210 C 285 250, 270 285, 285 310 L 540 310 L 540 0 Z" fill="#a6cf2d"/>
    <path d="M300 0 C 250 80, 340 140, 310 210 C 295 250, 280 285, 295 310 L 540 310 L 540 0 Z" fill="url(#frontBlue)"/>
  </svg>

  <div class="brand"><span class="brand__dot"></span><span>Harbor Ledger<br>Funds LLC</span></div>

  <div class="contact">
    <p class="contact__name">Daniel Reyes</p>
    <p class="contact__title">Manager</p>
    <p class="contact__address">PO BOX 123<br>your address<br>2nd street Kelport</p>
    <ul class="contact__list">
      <li class="contact__item">
        <svg class="contact__icon" viewBox="0 0 16 16" aria-hidden="true"><circle cx="8" cy="8" r="8" fill="#a6cf2d"/><path d="M5.2 4.3l1.4-.3.8 2-1 .7a5 5 0 0 0 2.2 2.2l.7-1 2 .8-.3 1.4c-3 .4-6.2-2.8-5.8-5.8z" fill="#1f3f94"/></svg>
        <span>555.555.5555</span>
      </li>
      <li class="contact__item">
        <svg class="contact__icon" viewBox="0 0 16 16" aria-hidden="true"><circle cx="8" cy="8" r="8" fill="#a6cf2d"/><rect x="4" y="5.2" width="8" height="5.6" fill="none" stroke="#1f3f94" stroke-width="1.1"/><path d="M4 5.4l4 3 4-3" fill="none" stroke="#1f3f94" stroke-width="1.1"/></svg>
        <span>info@harborledger.com</span>
      </li>
      <li class="contact__item">
        <svg class="contact__icon" viewBox="0 0 16 16" aria-hidden="true"><circle cx="8" cy="8" r="8" fill="#a6cf2d"/><circle cx="8" cy="8" r="4.2" fill="none" stroke="#1f3f94" stroke-width="1"/><ellipse cx="8" cy="8" rx="1.8" ry="4.2" fill="none" stroke="#1f3f94" stroke-width="1"/><path d="M3.8 8h8.4" stroke="#1f3f94" stroke-width="1"/></svg>
        <span>www.<span class="contact__web-accent">harborledgerfunds</span>.com</span>
      </li>
    </ul>
  </div>
</section>

<section class="card card--back" aria-label="Business card back">
  <div class="brand"><span class="brand__dot"></span><span>Harbor Ledger<br>Funds LLC</span></div>
</section>

</body>
</html>
```